Enterprise IT illustration needs a twist and uniquness

The attached Powerpoint shows four conceptual houses that consist of 5 / 6 building blocks. We will build a lot of content around this concept and want a design that looks crisp, in line with our brand colors guideline and with logo/ copyright embedded. Each building blocks should have unique color aligned with brand guideline so that content can easily aligned with the specific building block (by color). Look for a clean, modern design with a twist. Need the files also in formats where I can change text if needed at a later point.

```html
<!DOCTYPE html>
<html lang="en">
<head>
<meta charset="utf-8">
<title>Five Building Blocks – House Concepts</title>
<link href="https://fonts.googleapis.com/css2?family=Poppins:wght@400&family=Open+Sans:ital,wght@1,400;1,800&display=swap" rel="stylesheet">
<style>
  :root {
    --cyan: #26e0f7;
    --navy: #283583;
    --yellow: #fcd53b;
    --red: #ff3b5c;
    --orange: #f7a533;
    --grey-mark: #c8c8c8;
    --note: #6b6b6b;
    --paper: #ffffff;
  }
  html, body {
    margin: 0;
    padding: 0;
    width: 1200px;
    height: 1200px;
    overflow: hidden;
    background: var(--paper);
  }
  .canvas { display: block; width: 1200px; height: 1200px; }
  .block { fill: none; stroke-width: 10; stroke-linejoin: miter; }
  .roof { stroke: var(--cyan); stroke-linejoin: round; }
  .alerting { stroke: var(--navy); }
  .topology { stroke: var(--yellow); }
  .learn { stroke: var(--red); }
  .harvest { stroke: var(--orange); }
  .label { font-family: 'Poppins', sans-serif; font-weight: 400; font-size: 33px; }
  .num { font-family: 'Poppins', sans-serif; font-weight: 400; font-size: 66px; }
  .t-roof { fill: var(--cyan); }
  .t-alerting { fill: var(--navy); }
  .t-topology { fill: var(--yellow); }
  .t-learn { fill: var(--red); }
  .t-harvest { fill: var(--orange); }
  .concept-number { font-family: 'Open Sans', sans-serif; font-style: italic; font-weight: 800; font-size: 165px; fill: var(--grey-mark); }
  .note { font-family: 'Open Sans', sans-serif; font-style: italic; font-size: 35px; fill: var(--note); }
</style>
</head>
<body>
<svg class="canvas" viewBox="0 0 1920 1920" xmlns="http://www.w3.org/2000/svg">
  <text class="concept-number" x="88" y="195">2</text>

  <!-- House A: straight blocks -->
  <g class="house house-straight">
    <polygon class="block roof" points="595,113 290,338 898,338"/>
    <text class="num t-roof" x="458" y="310">5</text>
    <text class="label t-roof" x="517" y="300">Taking action</text>

    <rect class="block alerting" x="291" y="380" width="600" height="84"/>
    <text class="num t-alerting" x="355" y="445">4</text>
    <text class="label t-alerting" x="418" y="434">Business relevant alerting</text>

    <rect class="block topology" x="291" y="505" width="280" height="165"/>
    <text class="num t-topology" x="326" y="615">3</text>
    <text class="label t-topology" x="381" y="583">Topology</text>
    <text class="label t-topology" x="381" y="621">discovery</text>

    <rect class="block learn" x="611" y="505" width="280" height="165"/>
    <text class="num t-learn" x="660" y="615">2</text>
    <text class="label t-learn" x="721" y="585">Learn &amp;</text>
    <text class="label t-learn" x="721" y="623">Control</text>

    <rect class="block harvest" x="291" y="712" width="600" height="88"/>
    <text class="num t-harvest" x="374" y="780">1</text>
    <text class="label t-harvest" x="426" y="769">Qualtiy Data Harvesting</text>
  </g>

  <!-- House B: tilted edges -->
  <g class="house house-tilted">
    <polygon class="block roof" points="1373,116 1073,351 1672,351"/>
    <polygon class="block roof" points="1373,113 1095,340 1373,128" style="stroke-width:4"/>
    <text class="num t-roof" x="1236" y="323">5</text>
    <text class="label t-roof" x="1295" y="313">Taking action</text>

    <polygon class="block alerting" points="1073,400 1375,391 1672,400 1672,490 1073,490"/>
    <text class="num t-alerting" x="1136" y="472">4</text>
    <text class="label t-alerting" x="1200" y="460">Business relevant alerting</text>

    <polygon class="block topology" points="1073,539 1210,529 1352,539 1352,703 1073,703"/>
    <text class="num t-topology" x="1108" y="650">3</text>
    <text class="label t-topology" x="1163" y="617">Topology</text>
    <text class="label t-topology" x="1163" y="655">discovery</text>

    <polygon class="block learn" points="1394,539 1672,539 1672,703 1394,703 1385,620"/>
    <text class="num t-learn" x="1442" y="650">2</text>
    <text class="label t-learn" x="1502" y="618">Learn &amp;</text>
    <text class="label t-learn" x="1502" y="656">Control</text>

    <polygon class="block harvest" points="1073,752 1530,743 1672,752 1672,840 1073,840"/>
    <text class="num t-harvest" x="1156" y="820">1</text>
    <text class="label t-harvest" x="1208" y="810">Qualtiy Data Harvesting</text>
  </g>

  <!-- House C: tilted edges -->
  <g class="house house-tilted">
    <polygon class="block roof" points="579,903 280,1128 878,1128"/>
    <text class="num t-roof" x="443" y="1100">5</text>
    <text class="label t-roof" x="501" y="1090">Taking action</text>

    <polygon class="block alerting" points="280,1177 582,1168 878,1177 878,1265 280,1265"/>
    <text class="num t-alerting" x="343" y="1248">4</text>
    <text class="label t-alerting" x="406" y="1237">Business relevant alerting</text>

    <polygon class="block topology" points="280,1315 420,1305 557,1315 557,1478 280,1478"/>
    <text class="num t-topology" x="314" y="1425">3</text>
    <text class="label t-topology" x="369" y="1394">Topology</text>
    <text class="label t-topology" x="369" y="1432">discovery</text>

    <polygon class="block learn" points="600,1315 878,1315 878,1478 602,1478 591,1398"/>
    <text class="num t-learn" x="648" y="1425">2</text>
    <text class="label t-learn" x="709" y="1395">Learn &amp;</text>
    <text class="label t-learn" x="709" y="1433">Control</text>

    <polygon class="block harvest" points="280,1530 740,1521 878,1530 878,1615 280,1615"/>
    <text class="num t-harvest" x="364" y="1597">1</text>
    <text class="label t-harvest" x="414" y="1587">Qualtiy Data Harvesting</text>
  </g>

  <!-- House D: heavier tilted edges -->
  <g class="house house-heavy">
    <polygon class="block roof" points="1357,906 1048,1140 1665,1140"/>
    <polygon class="block roof" points="1357,903 1070,1128 1357,918" style="stroke-width:4"/>
    <text class="num t-roof" x="1216" y="1111">5</text>
    <text class="label t-roof" x="1275" y="1101">Taking action</text>

    <polygon class="block alerting" points="1053,1190 1360,1190 1660,1190 1660,1280 1053,1280"/>
    <polygon class="t-alerting" points="1053,1184 1360,1184 1660,1184 1660,1196 1360,1188 1053,1198"/>
    <text class="num t-alerting" x="1118" y="1260">4</text>
    <text class="label t-alerting" x="1180" y="1248">Business relevant alerting</text>

    <polygon class="block topology" points="1053,1325 1330,1325 1330,1495 1053,1495"/>
    <polygon class="t-topology" points="1053,1320 1330,1320 1330,1332 1190,1328 1053,1338"/>
    <text class="num t-topology" x="1088" y="1440">3</text>
    <text class="label t-topology" x="1143" y="1405">Topology</text>
    <text class="label t-topology" x="1143" y="1443">discovery</text>

    <polygon class="block learn" points="1375,1325 1660,1325 1660,1495 1375,1495"/>
    <polygon class="t-learn" points="1370,1325 1385,1325 1377,1408 1385,1495 1370,1495"/>
    <text class="num t-learn" x="1431" y="1440">2</text>
    <text class="label t-learn" x="1487" y="1403">Learn &amp;</text>
    <text class="label t-learn" x="1487" y="1441">Control</text>

    <polygon class="block harvest" points="1053,1540 1660,1540 1660,1635 1053,1635"/>
    <polygon class="t-harvest" points="1053,1535 1660,1535 1660,1555 1530,1545 1053,1553"/>
    <text class="num t-harvest" x="1138" y="1612">1</text>
    <text class="label t-harvest" x="1188" y="1603">Qualtiy Data Harvesting</text>
  </g>

  <text class="note" x="95" y="1852">NOTE: Kindly inform for any correction(s). I will effect them immediately</text>
</svg>
</body>
</html>
```